Employee Benefits Flyer for Recruiting

We are a Steel Product Supplier and Manufacturer in Toledo Ohio.

We would like to create an "attention getting", one-page handout to give prospective employees (both production and administrative) that illustrates all the benefits we offer as a company. An editable document would be preferable as we add more or change existing benefits in the future. Current benefits include:

Individual and Family Medical Insurance
Dental Insurance
Vision Insurance
Short Term Disability Insurance
Critical Illness and Accident Insurance
No Cost Life Insurance Policy
Education Cost Reimbursement
401K with Company Match
Profit Sharing
Attendance and Performance Bonuses
No Cost Legal Assistance
No Cost Counseling Services
No Cost Tobacco Cessation Coaching
No Cost College Planning Assistance
No Cost Work-Life Services
No Cost Employee Discounts
No Cost Legal Consultation
No Cost Financial Consultation
No Cost ID Theft Assistance
No Cost Tax Consultation Assistance
Up to 17 Days of Paid Time Off

Target Market(s)

Potential Employees

Industry/Entity Type

Industrial Manufacturing

Requirements
Must have
• Nicely laid out illustrations / engaging content

```html
<!DOCTYPE html>
<html lang="en">
<head>
<meta charset="utf-8">
<title>We Are Hiring – Benefits Flyer</title>
<link href="https://fonts.googleapis.com/css2?family=Anton&family=Oswald:wght@400;500;600&family=Montserrat:wght@500;600;700;800&display=swap" rel="stylesheet">
<style>
:root{
  --blue:#0d47a1;
  --blue-deep:#0a3a8c;
  --blue-bright:#1257c4;
  --orange:#f7941d;
  --orange-light:#fbb040;
  --white:#ffffff;
  --ink:#1d2a44;
  --page:#ececec;
}
*{margin:0;padding:0;box-sizing:border-box}
html,body{width:727px;height:1200px;overflow:hidden;background:var(--page)}
.canvas{position:relative;width:727px;height:1200px}
.flyer{position:absolute;left:0;top:130px;width:727px;height:940px;background:var(--white);overflow:hidden;box-shadow:0 6px 18px rgba(0,0,0,.18)}
.abs{position:absolute}

/* header */
.header{left:0;top:0;width:727px;height:349px;background:linear-gradient(120deg,var(--blue-deep) 0%,var(--blue) 55%,#2a6fd6 100%)}
.header-photo{right:0;top:0;width:380px;height:349px;background:linear-gradient(160deg,#3f7fd9 0%,#1f55a8 45%,#e07a2a 75%,#2b2f3c 100%);opacity:.9}
.title-small{left:46px;top:36px;font:800 56px/1 'Montserrat',sans-serif;color:var(--white);letter-spacing:2px}
.title-big{left:44px;top:96px;font:400 168px/1 'Anton',sans-serif;letter-spacing:-2px;background:linear-gradient(180deg,var(--orange-light),var(--orange));-webkit-background-clip:text;background-clip:text;color:transparent}
.roles{left:46px;top:262px;font:400 29px/1 'Oswald',sans-serif;color:var(--white);letter-spacing:-.5px}
.benefits-band{left:0;top:307px;width:727px;height:42px}
.benefits-title{left:46px;top:312px;font:800 30px/1 'Montserrat',sans-serif;color:var(--blue);letter-spacing:.5px}

/* benefits list */
.benefit{display:flex;align-items:center;gap:12px;font:500 12.5px/1.2 'Montserrat',sans-serif;color:var(--ink)}
.icon{flex:none;width:32px;height:32px}
.photo{background:var(--white);padding:7px;box-shadow:0 3px 8px rgba(0,0,0,.3)}
.photo div{width:100%;height:100%}

/* savings */
.savings{left:0;top:588px;width:727px;height:205px;background:linear-gradient(90deg,var(--blue-deep),var(--blue-bright))}
.save-title{left:48px;top:600px;font:500 26px/1.05 'Oswald',sans-serif;color:var(--white)}
.save-title .light{font-weight:400}
.save-title .hot{color:var(--orange);display:block}
.illustration{left:14px;top:660px;width:222px;height:126px;border-radius:4px;background:linear-gradient(135deg,#3d7ee0,#8fb4ee 60%,#f7a23a)}
.perk{font:500 11px/1 'Montserrat',sans-serif;color:var(--white);white-space:nowrap}
.perk b{font:500 13px/1 'Oswald',sans-serif;color:var(--orange);margin-right:6px}

/* footer */
.resume-title{left:48px;top:804px;font:500 31px/1 'Oswald',sans-serif;color:var(--orange)}
.email{left:48px;top:846px;font:500 20px/1 'Montserrat',sans-serif;color:var(--ink);display:flex;align-items:center;gap:8px}
.phone-pill{left:48px;top:880px;height:30px;display:flex;border-radius:15px;overflow:hidden;font:700 19px/30px 'Montserrat',sans-serif}
.phone-pill .label{background:var(--blue);color:var(--white);padding:0 10px}
.phone-pill .number{background:var(--orange);color:var(--blue);padding:0 12px 0 6px}
.divider{width:1px;background:#555}
.address{left:380px;top:846px;font:500 12.5px/1.25 'Montserrat',sans-serif;color:var(--ink)}
.brand{left:515px;top:840px;width:205px;display:flex;align-items:center;justify-content:center;gap:8px;font:800 17px/1 'Montserrat',sans-serif;color:var(--blue)}
.brand-dot{width:22px;height:22px;border-radius:50%;background:var(--blue)}
</style>
</head>
<body>
<div class="canvas">
<main class="flyer">

  <section class="abs header"></section>
  <div class="abs header-photo" role="img" aria-label="Photo of a smiling steel worker in hard hat and safety vest beside an office professional, in front of the plant"></div>
  <div class="abs title-small">WE ARE</div>
  <h1 class="abs title-big">HIRING</h1>
  <div class="abs roles">PRODUCTION &amp; ADMINISTRATIVE</div>

  <svg class="abs benefits-band" width="727" height="42" viewBox="0 0 727 42">
    <polygon points="0,0 300,0 325,42 0,42" fill="var(--orange)"/>
    <rect x="0" y="38" width="727" height="4" fill="var(--orange)"/>
  </svg>
  <h2 class="abs benefits-title">OUR BENEFITS</h2>

  <ul class="benefit-list" style="list-style:none">
    <li class="abs benefit" style="left:47px;top:373px"><svg class="icon" viewBox="0 0 32 32"><circle cx="16" cy="16" r="16" fill="var(--blue)"/><path d="M16 8l7 3v5c0 4-3 7-7 8-4-1-7-4-7-8v-5z" fill="var(--orange)"/></svg>Individual and Family<br>Medical Insurance</li>
    <li class="abs benefit" style="left:47px;top:411px"><svg class="icon" viewBox="0 0 32 32"><circle cx="16" cy="16" r="16" fill="var(--blue)"/><circle cx="16" cy="15" r="7" fill="var(--orange)"/></svg>Dental Insurance</li>
    <li class="abs benefit" style="left:47px;top:448px"><svg class="icon" viewBox="0 0 32 32"><circle cx="16" cy="16" r="16" fill="var(--blue)"/><circle cx="16" cy="16" r="7" fill="none" stroke="var(--orange)" stroke-width="2.5"/></svg>Short Term<br>Disability Insurance</li>
    <li class="abs benefit" style="left:47px;top:492px"><svg class="icon" viewBox="0 0 32 32"><circle cx="16" cy="16" r="16" fill="var(--blue)"/><path d="M16 8l7 3v5c0 4-3 7-7 8-4-1-7-4-7-8v-5z" fill="var(--orange)"/><path d="M12 16l3 3 5-6" stroke="var(--white)" stroke-width="2" fill="none"/></svg>Critical Illness and<br>Accident Insurance</li>
    <li class="abs benefit" style="left:47px;top:534px"><svg class="icon" viewBox="0 0 32 32"><circle cx="16" cy="16" r="16" fill="var(--blue)"/><ellipse cx="16" cy="16" rx="9" ry="5" fill="none" stroke="var(--orange)" stroke-width="2"/><circle cx="16" cy="16" r="2.5" fill="var(--orange)"/></svg>Vision Insurance</li>

    <li class="abs benefit" style="left:271px;top:373px"><svg class="icon" viewBox="0 0 32 32"><circle cx="16" cy="16" r="16" fill="var(--blue)"/><path d="M6 14l10-5 10 5-10 5z" fill="var(--orange)"/></svg>Education Cost<br>Reimbursement</li>
    <li class="abs benefit" style="left:271px;top:412px"><svg class="icon" viewBox="0 0 32 32"><circle cx="16" cy="16" r="16" fill="var(--blue)"/><rect x="10" y="15" width="3" height="7" fill="var(--orange)"/><rect x="15" y="11" width="3" height="11" fill="var(--orange)"/><rect x="20" y="13" width="3" height="9" fill="var(--orange)"/></svg>401K with<br>Company Match</li>
    <li class="abs benefit" style="left:271px;top:451px"><svg class="icon" viewBox="0 0 32 32"><circle cx="16" cy="16" r="16" fill="var(--blue)"/><circle cx="16" cy="16" r="7" fill="var(--orange)"/></svg>Profit Sharing</li>
    <li class="abs benefit" style="left:271px;top:492px"><svg class="icon" viewBox="0 0 32 32"><circle cx="16" cy="16" r="16" fill="var(--blue)"/><circle cx="16" cy="16" r="10" fill="var(--orange)"/><circle cx="16" cy="16" r="6" fill="var(--blue)"/></svg>Attendance and<br>Performance Bonuses</li>
    <li class="abs benefit" style="left:271px;top:534px"><svg class="icon" viewBox="0 0 32 32"><circle cx="16" cy="16" r="16" fill="var(--blue)"/><rect x="9" y="10" width="14" height="12" rx="1" fill="var(--orange)"/><rect x="9" y="10" width="14" height="3" fill="var(--white)"/></svg>Up to 17 Days of<br>Paid Time Off</li>
  </ul>

  <div class="abs photo" style="left:468px;top:362px;width:178px;height:130px;transform:rotate(-3deg)"><div role="img" aria-label="Photo of a steel cutting machine throwing sparks" style="background:linear-gradient(135deg,#1a1410,#6b3a1a 45%,#f5b041 60%,#2a1a10)"></div></div>
  <div class="abs photo" style="left:512px;top:461px;width:178px;height:124px;transform:rotate(4deg)"><div role="img" aria-label="Photo of a plasma cutting table on the production floor" style="background:linear-gradient(160deg,#5a4a3a,#8a6e52 40%,#c0392b 70%,#3a3029)"></div></div>

  <section class="abs savings"></section>
  <h2 class="abs save-title">OPPORTUNITY <span class="light">TO</span><span class="hot">SAVE YOUR MONEY</span></h2>
  <div class="abs illustration" role="img" aria-label="Illustration of people beside rising bar chart with coins and an upward arrow"></div>

  <ul style="list-style:none">
    <li class="abs perk" style="left:250px;top:617px"><b>NO COST</b>Legal Assistance</li>
    <li class="abs perk" style="left:250px;top:646px"><b>NO COST</b>Counseling Services</li>
    <li class="abs perk" style="left:250px;top:675px"><b>NO COST</b>Tobacco Cessation Coaching</li>
    <li class="abs perk" style="left:250px;top:705px"><b>NO COST</b>College Planning Assistance</li>
    <li class="abs perk" style="left:250px;top:734px"><b>NO COST</b>Work-Life Services</li>
    <li class="abs perk" style="left:250px;top:764px"><b>NO COST</b>Life Insurance Policy</li>
    <li class="abs perk" style="left:478px;top:617px"><b>NO COST</b>Employee Discounts</li>
    <li class="abs perk" style="left:478px;top:646px"><b>NO COST</b>Legal Consultation</li>
    <li class="abs perk" style="left:478px;top:675px"><b>NO COST</b>Financial Consultation</li>
    <li class="abs perk" style="left:478px;top:705px"><b>NO COST</b>ID Theft Assistance</li>
    <li class="abs perk" style="left:478px;top:734px"><b>NO COST</b>Tax Consultation Assistance</li>
  </ul>

  <svg class="abs" style="left:0;top:770px" width="727" height="30" viewBox="0 0 727 30">
    <polygon points="480,0 727,0 727,8 500,8 480,28 0,28 0,23 476,23" fill="var(--white)"/>
    <polyline points="0,25 478,25 498,6 727,6" fill="none" stroke="var(--orange)" stroke-width="2.5"/>
  </svg>

  <footer>
    <div class="abs resume-title">EMAIL YOUR RESUME AT</div>
    <div class="abs email"><svg width="18" height="13" viewBox="0 0 18 13"><rect width="18" height="13" fill="var(--blue)"/><path d="M0 0l9 7 9-7" stroke="var(--white)" stroke-width="1.5" fill="none"/></svg>info@keystone-metal.com</div>
    <div class="abs phone-pill"><span class="label">Toll Free No</span><span class="number">800-555-0148</span></div>
    <div class="abs divider" style="left:362px;top:812px;height:115px"></div>
    <svg class="abs" style="left:380px;top:812px" width="24" height="26" viewBox="0 0 24 26"><path d="M12 1a9 9 0 0 1 9 9c0 7-9 15-9 15S3 17 3 10a9 9 0 0 1 9-9z" fill="var(--blue)"/><circle cx="12" cy="10" r="3.5" fill="var(--white)"/></svg>
    <address class="abs address" style="font-style:normal">Keystone Metal<br>Works, Inc.<br>120 West Harbor<br>Avenue Toledo,<br>OH 43600</address>
    <div class="abs divider" style="left:500px;top:812px;height:115px"></div>
    <div class="abs brand"><span class="brand-dot"></span>KEYSTONE METAL</div>
  </footer>

</main>
</div>
</body>
</html>
```